Fresh, modern, fun business card for pediatric dental practice

Need a business card for fresh, modern, fun pediatric dental practice

Clean look that matches our website's font and colors

We prefer the look of curved corners on business cards

Target Market(s)

parents (mothers) of young children, professionals, mid-high class

Industry/Entity Type

Dental

Contact Information for Business Card

Maplebrook Pediatric Dentistry
482 Quarry Lane
Suite 517
Fernwick, PA 17990
717.555.0193
www.maplebrookkidsdental.example

Mei-Ran Tsai, DMD
Corinne Walbeck, DMD
(we are working on our email address, but we would like that on the card as well)

Font styles to use
Sans Serif

Requirements
Must have
• All info; we would also like to make cards for individual staff members
• colors from our website and color palatte, attatched
• use same font and design as website for branding
Nice to have
• clean, simple card that has a pop of color
• we would like to see a few designs with our tag line "where smiles get brighter"
• we are not sure if we want to have it on there or not
• we would like to see a few designs incorporating the ribbon graphic on our website where the word WELCOME is

```html
<!DOCTYPE html>
<html lang="en">
<head>
<meta charset="utf-8">
<title>Maplebrook Pediatric Dentistry – Business Cards</title>
<link href="https://fonts.googleapis.com/css2?family=Roboto:wght@500;700&family=Lato:wght@400;700&display=swap" rel="stylesheet">
<style>
  :root {
    --pink: #d22b8f;
    --pink-deep: #c72585;
    --yellow: #f4b223;
    --ink: #555555;
    --paper: #ffffff;
    --backdrop: #3a3a3a;
  }
  * { box-sizing: border-box; margin: 0; padding: 0; }
  html, body { width: 1200px; height: 960px; overflow: hidden; }
  body { background: var(--backdrop); font-family: "Lato", sans-serif; position: relative; }

  .card {
    position: absolute;
    width: 475px;
    height: 270px;
    border-radius: 12px;
    box-shadow: 0 3px 8px rgba(0,0,0,.45);
    overflow: hidden;
  }
  .card--front { background: var(--paper); }
  .card--back { background: var(--pink); }

  .card--one { left: 110px; top: 184px; }
  .card--two { left: 611px; top: 184px; }
  .card--three { left: 110px; top: 502px; }
  .card--four { left: 611px; top: 502px; }

  .brand {
    position: absolute;
    display: flex;
    flex-direction: column;
    align-items: center;
    transform: translateX(-50%);
    font-family: "Lato", sans-serif;
    text-align: center;
    white-space: nowrap;
  }
  .brand__dot {
    width: 26px; height: 26px;
    border-radius: 50%;
    background: var(--yellow);
    margin-bottom: 8px;
  }
  .brand__name { font-size: 33px; font-weight: 700; line-height: 1; letter-spacing: 1px; color: var(--yellow); }
  .brand__sub { font-size: 17px; font-weight: 400; line-height: 1; letter-spacing: 1.5px; margin-top: 5px; color: var(--pink); }
  .brand--light .brand__dot { background: var(--paper); }
  .brand--light .brand__name,
  .brand--light .brand__sub { color: var(--paper); }

  .divider {
    position: absolute;
    width: 2px;
    background: var(--yellow);
  }

  .contact { position: absolute; }
  .contact__person {
    font-family: "Roboto", sans-serif;
    font-weight: 700;
    font-size: 20px;
    color: var(--pink);
    white-space: nowrap;
  }
  .contact__title { font-weight: 500; color: var(--yellow); }
  .contact__practice {
    margin-top: 14px;
    font-weight: 700;
    font-size: 11px;
    color: var(--pink);
  }
  .contact__address { font-size: 11px; line-height: 15px; color: var(--ink); }
  .contact__list { list-style: none; margin-top: 12px; }
  .contact__item {
    display: flex; align-items: center; gap: 6px;
    font-size: 10.5px; line-height: 17px; color: var(--ink); white-space: nowrap;
  }
  .icon { width: 13px; height: 13px; flex: none; }

  .pattern {
    position: absolute; inset: 0;
    background: radial-gradient(circle at 50% 50%, var(--pink) 0%, var(--pink-deep) 100%);
  }
  .pattern-label {
    position: absolute;
    left: 50%; top: 50%;
    transform: translate(-50%, -50%);
    padding: 8px 14px;
    background: var(--pink);
    text-align: center;
    white-space: nowrap;
  }
  .pattern-label .brand__name { display: block; font-size: 30px; color: var(--paper); }
  .pattern-label .brand__sub { display: block; font-size: 15px; color: var(--paper); }
</style>
</head>
<body>

<svg width="0" height="0" style="position:absolute" aria-hidden="true">
  <defs>
    <symbol id="icon-phone" viewBox="0 0 16 16">
      <circle cx="8" cy="8" r="8" fill="#d22b8f"/>
      <path d="M5.2 3.8l1.4 1.6-.7 1.1c.5 1.2 1.4 2.1 2.6 2.6l1.1-.7 1.6 1.4-.9 1.4c-3-.4-5.1-2.5-5.5-5.5z" fill="#fff"/>
    </symbol>
    <symbol id="icon-mail" viewBox="0 0 16 16">
      <circle cx="8" cy="8" r="8" fill="#d22b8f"/>
      <rect x="4" y="5.2" width="8" height="5.6" rx=".6" fill="#fff"/>
      <path d="M4.3 5.6L8 8.3l3.7-2.7" stroke="#d22b8f" stroke-width=".9" fill="none"/>
    </symbol>
    <symbol id="icon-web" viewBox="0 0 16 16">
      <circle cx="8" cy="8" r="8" fill="#d22b8f"/>
      <circle cx="8" cy="8" r="4" fill="none" stroke="#fff" stroke-width="1"/>
      <path d="M4 8h8M8 4c-1.6 2.4-1.6 5.6 0 8M8 4c1.6 2.4 1.6 5.6 0 8" stroke="#fff" stroke-width=".8" fill="none"/>
    </symbol>
  </defs>
</svg>

<section class="card card--front card--one">
  <div class="brand" style="left:124px; top:82px;">
    <span class="brand__dot"></span>
    <span class="brand__name">maplebrook</span>
    <span class="brand__sub">pediatric dentistry</span>
  </div>
  <div class="divider" style="left:236px; top:66px; height:142px;"></div>
  <div class="contact" style="left:263px; top:63px;">
    <p class="contact__person">Mei-Ran Tsai, <span class="contact__title">DMD</span></p>
    <p class="contact__practice">Maplebrook Pediatric Dentistry</p>
    <p class="contact__address">482 Quarry Lane, Suite 517<br>Fernwick, PA 17990</p>
    <ul class="contact__list">
      <li class="contact__item"><svg class="icon"><use href="#icon-phone"/></svg>717.555.0193</li>
      <li class="contact__item"><svg class="icon"><use href="#icon-mail"/></svg>info@maplebrookkidsdental.example</li>
      <li class="contact__item"><svg class="icon"><use href="#icon-web"/></svg>www.maplebrookkidsdental.example</li>
    </ul>
  </div>
</section>

<section class="card card--back card--two">
  <div class="brand brand--light" style="left:237px; top:78px;">
    <span class="brand__dot"></span>
    <span class="brand__name">maplebrook</span>
    <span class="brand__sub">pediatric dentistry</span>
  </div>
</section>

<section class="card card--front card--three">
  <div class="brand" style="left:113px; top:82px;">
    <span class="brand__dot"></span>
    <span class="brand__name">maplebrook</span>
    <span class="brand__sub">pediatric dentistry</span>
  </div>
  <div class="divider" style="left:223px; top:66px; height:142px;"></div>
  <div class="contact" style="left:247px; top:63px;">
    <p class="contact__person">Corinne Walbeck, <span class="contact__title">DMD</span></p>
    <p class="contact__practice">Maplebrook Pediatric Dentistry</p>
    <p class="contact__address">482 Quarry Lane, Suite 517<br>Fernwick, PA 17990</p>
    <ul class="contact__list">
      <li class="contact__item"><svg class="icon"><use href="#icon-phone"/></svg>717.555.0193</li>
      <li class="contact__item"><svg class="icon"><use href="#icon-mail"/></svg>info@maplebrookkidsdental.example</li>
      <li class="contact__item"><svg class="icon"><use href="#icon-web"/></svg>www.maplebrookkidsdental.example</li>
    </ul>
  </div>
</section>

<section class="card card--back card--four">
  <div class="pattern" role="img" aria-label="Repeating pattern of small orange sun motifs on pink"></div>
  <div class="pattern-label">
    <span class="brand__name">maplebrook</span>
    <span class="brand__sub">pediatric dentistry</span>
  </div>
</section>

</body>
</html>
```